Redesign Of Current Landing Page

I need to redesign this landing page https://www.brightlanepromo.biz/?page=landing&landing=23 (Please do not opt in because when you do it will show you the home page. Please clear your cookies before going to this url above to view the 1 page landing page.)

Please use my updated website as a reference for colors and logo.
http://sitecradlewerk.com/dh/bpq/index.html

I would like the call to action to be a button that opens into a lead form...

Button would be "Download Samples"

Target Market(s)

small business owners

Industry/Entity Type

Marketing

Number of Pages Required

1 page

Colors

Designer to choose colors to be used in the design.

Requirements
Must have
• must be full responsive on all devices
Nice to have
• must have a legitimate professional apeal to it
Should not have
• open

```html
<!DOCTYPE html>
<html lang="en">
<head>
<meta charset="utf-8">
<title>BLPG – Attract More Customers</title>
<link rel="stylesheet" href="https://fonts.googleapis.com/css2?family=Open+Sans:ital,wght@0,400;0,600;0,700;1,400&family=Oswald:wght@500;700&display=swap">
<style>
:root{
  --blue:#1a6fbf;
  --blue-dark:#1d5d9e;
  --orange:#fda400;
  --ink:#333333;
  --muted:#8a8a8a;
  --white:#ffffff;
  --footer:#f4f4f4;
  --dark:#1b2129;
}
*{margin:0;padding:0;box-sizing:border-box}
html,body{width:697px;height:1200px;overflow:hidden;background:var(--white)}
body{position:relative;font-family:"Open Sans",Arial,sans-serif;color:var(--ink)}
.abs{position:absolute}

/* header */
.site-header{left:0;top:0;width:697px;height:48px;background:var(--white);border-bottom:3px solid var(--blue)}
.brand{left:77px;top:13px;display:flex;align-items:center;gap:6px}
.brand-dot{width:20px;height:20px;border-radius:50%;background:var(--blue-dark)}
.brand-name{font-family:"Open Sans",sans-serif;font-weight:700;font-size:18px;color:var(--ink);letter-spacing:.5px}
.main-nav{left:252px;top:19px;display:flex;gap:0;font-size:7px;font-weight:600;text-transform:uppercase}
.main-nav a{text-decoration:none;color:var(--ink);margin-right:27px}
.main-nav a.active{color:var(--blue)}
.search-btn{left:599px;top:14px;width:21px;height:21px;border-radius:50%;background:#e4e4e4}

/* hero */
.hero{left:0;top:51px;width:697px;height:287px;background:linear-gradient(100deg,#5f6e80 0%,#8a93a0 30%,#7c6a5a 60%,#3e3226 100%)}
.hero-copy{left:70px;top:72px;width:180px;text-align:center;color:var(--white)}
.hero-kicker{font-family:"Oswald",sans-serif;font-weight:700;font-size:17px;letter-spacing:.5px}
.hero-title{font-family:"Oswald",sans-serif;font-weight:700;font-size:34px;line-height:1.05;letter-spacing:1px}
.hero-sub{font-size:11px;line-height:16px;margin-top:6px}
.cta{display:inline-block;margin-top:14px;background:var(--orange);color:var(--white);font-size:7px;font-weight:600;padding:8px 12px;border-radius:12px;text-transform:uppercase}
.dots{left:326px;top:246px;display:flex;gap:10px}
.dots span{width:9px;height:9px;border-radius:50%;border:1.5px solid var(--white)}
.dots span.on{background:var(--orange);border-color:var(--orange)}

/* how */
.how-photo{left:0;top:338px;width:697px;height:189px}
.how{left:0;top:338px;width:697px;height:189px}
.how-copy{left:365px;top:368px;width:260px;color:var(--white)}
.how-copy h2{font-size:14px;font-weight:600;margin-bottom:10px}
.how-copy p{font-size:5.5px;line-height:12px;margin-bottom:8px}

/* why */
.why-title{left:0;top:557px;width:697px;text-align:center;font-size:14px;font-weight:600;color:var(--ink)}
.feature{width:160px;display:flex;gap:10px}
.feature-icon{flex:none;width:31px;height:31px;border-radius:50%;border:1px solid var(--blue);display:flex;align-items:center;justify-content:center}
.feature h3{font-size:8px;font-weight:400;line-height:12px;color:var(--ink)}
.feature p{font-size:5.5px;line-height:11px;color:var(--muted);margin-top:2px}

/* imagine */
.imagine{left:0;top:760px;width:697px;height:185px;background:linear-gradient(180deg,#2a3340 0%,#1b2129 55%,#3a3124 100%)}
.imagine-copy{left:130px;top:805px;width:437px;text-align:center;color:var(--white)}
.imagine-copy h2{font-size:14px;font-weight:600;margin-bottom:9px}
.imagine-copy p{font-size:5.5px;line-height:12px;margin-bottom:7px}

/* testimonial */
.avatar{left:317px;top:971px;width:62px;height:62px;border-radius:50%;border:2px solid #d8d8d8;background:linear-gradient(180deg,#dedede,#c7c0b8)}
.quote{left:92px;top:1036px;width:513px;text-align:center;font-style:italic;font-size:5.5px;line-height:13px;color:#555}
.qmark{font-family:Georgia,serif;font-size:18px;color:#999}
.author{left:0;top:1086px;width:697px;text-align:center;font-size:6.5px;font-weight:700;color:var(--blue)}
.place{left:0;top:1097px;width:697px;text-align:center;font-size:5.5px;font-weight:600;color:#666}

/* footer */
.site-footer{left:0;top:1135px;width:697px;height:65px;background:var(--footer);border-top:2px solid var(--blue)}
.footer-brand{left:77px;top:1160px}
.footer-links{left:171px;top:1157px;font-size:5.5px;color:#666;line-height:14px}
.social{left:548px;top:1161px;display:flex;gap:4px}
.social span{width:16px;height:16px;border-radius:50%}
</style>
</head>
<body>

<header class="site-header abs">
</header>
<div class="brand abs"><span class="brand-dot"></span><span class="brand-name">BLPG</span></div>
<nav class="main-nav abs">
  <a class="active" href="#">Home</a><a href="#">About Us</a><a href="#">Services</a><a href="#">Testimonials</a><a href="#">Blog</a><a href="#">Contact Us</a>
</nav>
<div class="search-btn abs">
  <svg width="21" height="21" viewBox="0 0 21 21"><circle cx="9.8" cy="9.8" r="2.2" fill="none" stroke="#888" stroke-width="1"/><line x1="11.4" y1="11.4" x2="13" y2="13" stroke="#888" stroke-width="1"/></svg>
</div>

<section class="hero abs" role="img" aria-label="Seaside resort terrace with dining tables at sunset"></section>
<div class="hero-copy abs">
  <div class="hero-kicker">ATTRACT MORE</div>
  <div class="hero-title">CUSTOMERS</div>
  <p class="hero-sub">Who spend more money with your business more often!</p>
  <span class="cta">Download Samples</span>
</div>
<div class="dots abs"><span class="on"></span><span></span><span></span></div>

<section class="how abs">
  <svg width="697" height="189" viewBox="0 0 697 189">
    <defs>
      <linearGradient id="poolTone" x1="0" y1="0" x2="0" y2="1">
        <stop offset="0" stop-color="#e9c27c"/><stop offset=".45" stop-color="#6e8ea8"/><stop offset="1" stop-color="#1c3550"/>
      </linearGradient>
    </defs>
    <rect width="697" height="189" fill="var(--orange)"/>
    <path d="M0 0H320Q360 95 320 189H0Z" fill="url(#poolTone)" role="img" aria-label="Infinity pool with loungers and umbrellas at dusk"/>
    <path d="M320 0Q360 95 320 189" fill="none" stroke="#fff" stroke-width="2"/>
  </svg>
</section>
<div class="how-copy abs">
  <h2>HOW CAN WE DO IT?</h2>
  <p>We help fill empty rooms for thousands of hotels and resorts in hundreds of destinations around the world as well as the major cruise lines. Hotels and resorts are rarely full so when we place someone in their empty rooms, they end up making it up when travelers spend money on room service, spa services, eat at their in-house restaurants, casino and take advantage of other amenities that drive revenue</p>
  <p>We also help over 18,000 restaurants, electronic manufacturers, the major gas companies and top grocery chains in the U.S and Canada increase brand awareness as well as increase customer loyalty</p>
</div>

<h2 class="why-title abs">WHY OFFER INCENTIVES TO CUSTOMERS?</h2>

<div class="feature abs" style="left:77px;top:598px">
  <div class="feature-icon"><svg width="14" height="14" viewBox="0 0 14 14" fill="var(--blue)"><rect x="1" y="12" width="12" height="1"/><rect x="2" y="7" width="2" height="5"/><rect x="5" y="4" width="2" height="8"/><rect x="8" y="6" width="2" height="6"/><rect x="11" y="3" width="2" height="9"/></svg></div>
  <div><h3>Increase Responses From Your Existing Ads</h3><p>Phasellus facilisis, nunc in undo tump lacin auctor, eros lacus...</p></div>
</div>
<div class="feature abs" style="left:268px;top:598px">
  <div class="feature-icon"><svg width="14" height="14" viewBox="0 0 14 14"><path d="M2 12L8 6" stroke="var(--blue)" stroke-width="2.2" stroke-linecap="round"/><circle cx="10" cy="4" r="3" fill="none" stroke="var(--blue)" stroke-width="1.6"/></svg></div>
  <div><h3>#1 Sales Closing Tool - Gift w/ Purchase</h3><p>Phasellus facilisis, nunc in undo tump lacin auctor, eros lacus...</p></div>
</div>
<div class="feature abs" style="left:463px;top:598px">
  <div class="feature-icon"><svg width="14" height="14" viewBox="0 0 14 14"><path d="M7 1l1.8 4 4.2.4-3.2 2.8 1 4.2L7 10.2 3.2 12.4l1-4.2L1 5.4l4.2-.4z" fill="none" stroke="var(--blue)" stroke-width="1.2" stroke-linejoin="round"/></svg></div>
  <div><h3>Build Brand Awareness and Trust</h3><p>Phasellus facilisis, nunc in undo tump lacin auctor, eros lacus...</p></div>
</div>
<div class="feature abs" style="left:77px;top:677px">
  <div class="feature-icon"><svg width="14" height="14" viewBox="0 0 14 14"><path d="M1 7a6 5 0 0 1 12 0z" fill="none" stroke="var(--blue)" stroke-width="1.2"/><path d="M7 7v5a1.2 1.2 0 0 1-2.4 0" fill="none" stroke="var(--blue)" stroke-width="1.2"/></svg></div>
  <div><h3>Insure The Sale Over Your Competition</h3><p>Phasellus facilisis, nunc in undo tump lacin auctor, eros lacus...</p></div>
</div>
<div class="feature abs" style="left:268px;top:677px">
  <div class="feature-icon"><svg width="14" height="14" viewBox="0 0 14 14"><rect x="1" y="4" width="12" height="8" rx="1" fill="var(--blue)"/><rect x="5" y="2" width="4" height="2.4" fill="none" stroke="var(--blue)" stroke-width="1"/><rect x="6" y="7" width="2" height="1.5" fill="#fff"/></svg></div>
  <div><h3>Boost Repeat and Referral Business-</h3><p>Phasellus facilisis, nunc in undo tump lacin auctor, eros lacus...</p></div>
</div>
<div class="feature abs" style="left:463px;top:677px">
  <div class="feature-icon"><span style="color:var(--blue);font-size:15px;font-weight:600">$</span></div>
  <div><h3>Improve Retention Rates</h3><p>Phasellus facilisis, nunc in undo tump lacin auctor, eros lacus...</p></div>
</div>

<section class="imagine abs" role="img" aria-label="Modern glass building lit up at night among trees"></section>
<div class="imagine-copy abs">
  <h2>IMAGINE</h2>
  <p>being able to create exciting give away promotions that will boost your sales without ever having to worry about cost. Brightlane Promo Group, Inc. provides high-perceived value promotional incentives to businesses that want to advertise an exciting Give Away that will instantly attract more customers from your existing advertising efforts.</p>
  <p>Your business can give away incentive certificates that are redeemable for luxury hotel &amp; resort stays with airfare included, cruises, cash for gas, groceries, dining and even electronic goods.</p>
</div>

<div class="avatar abs" role="img" aria-label="Portrait photo of the client"></div>
<span class="qmark abs" style="left:92px;top:1030px">&ldquo;</span>
<p class="quote abs">I began using your incentives two years ago to boost lead generation efforts. I have experienced a 63% increase in lead captures. And, even more importantly, my sales have increased as well. The ability to offer unlimited certificates and not having to pay for each certificate I give away is perhaps the best feature of the program, but having the flexibility to email or print certificates for my customers is also wonderful. I even use your html banners to automate my promotions right on my website!</p>
<span class="qmark abs" style="left:528px;top:1066px">&rdquo;</span>
<div class="author abs">DAN R.</div>
<div class="place abs">HARLOW SPRINGS, TN</div>

<footer class="site-footer abs"></footer>
<div class="brand footer-brand abs" style="top:1160px"><span class="brand-dot"></span><span class="brand-name">BLPG</span></div>
<div class="footer-links abs">HOME | ABOUT US | SERVICES | TESTIMONIALS | BLOG | CONTACT US<br>COPYRIGHTS © BLPG . 2017 | ALL RIGHTS RESERVED.</div>
<div class="social abs"><span style="background:#1f3a6e"></span><span style="background:#2b9fe0"></span><span style="background:#e0332c"></span><span style="background:#b08a55"></span></div>

</body>
</html>
```